Modern Business Card

Modern professional business card with more than just logo and demographic info. Something memorable.

We are a trendy/modern chiropractic group with an emphasis on neurology, hence the minimalist-type brain logo. We want to convey that modern and technical aspect with professionalism and the elite nature of our practice environment.

```html
<!DOCTYPE html>
<html lang="en">
<head>
<meta charset="utf-8">
<title>Northline Chiropractic – Business Card</title>
<link href="https://fonts.googleapis.com/css2?family=Open+Sans:wght@400;700&display=swap" rel="stylesheet">
<style>
  :root {
    --page: #6b6b6d;
    --card: #323234;
    --card-deep: #2a2a2c;
    --accent: #3f7cc4;
    --ink: #ffffff;
    --ink-soft: #e6e6e8;
    --emboss: #27272a;
  }
  * { margin: 0; padding: 0; box-sizing: border-box; }
  html, body {
    width: 1200px;
    height: 1125px;
    overflow: hidden;
    background: var(--page);
    font-family: "Open Sans", sans-serif;
  }
  .sheet {
    width: 1200px;
    height: 1125px;
    display: flex;
    flex-direction: column;
    align-items: center;
    justify-content: center;
    gap: 44px;
  }
  .card {
    position: relative;
    width: 840px;
    height: 480px;
    background: var(--card);
    border-bottom: 9px solid var(--accent);
    box-shadow: 0 10px 24px rgba(0,0,0,0.35);
  }

  /* back side */
  .card--back {
    display: flex;
    align-items: center;
    justify-content: center;
  }
  .brand--embossed {
    display: flex;
    align-items: center;
    gap: 22px;
    color: var(--emboss);
  }
  .brand--embossed .brand__dot { background: var(--emboss); }

  /* shared brand block */
  .brand__dot {
    width: 34px;
    height: 34px;
    border-radius: 50%;
    flex: none;
  }
  .brand__name {
    font-weight: 700;
    font-size: 36px;
    line-height: 1.05;
    letter-spacing: 1px;
    text-transform: uppercase;
  }

  /* front side */
  .card--front {
    display: flex;
    align-items: center;
    padding: 0 56px;
  }
  .brand--front {
    display: flex;
    align-items: center;
    gap: 18px;
    width: 370px;
    color: var(--ink);
  }
  .brand--front .brand__dot { background: var(--accent); }
  .brand--front .brand__name { font-size: 32px; }
  .divider {
    width: 2px;
    height: 200px;
    background: var(--accent);
    margin: 0 26px 0 12px;
  }
  .contact { color: var(--ink); }
  .contact__name {
    color: var(--accent);
    font-weight: 700;
    font-size: 28px;
    letter-spacing: 1px;
    text-transform: uppercase;
    line-height: 1.1;
  }
  .contact__role {
    font-size: 20px;
    color: var(--ink-soft);
    margin-bottom: 16px;
  }
  .contact__address {
    font-size: 20px;
    line-height: 1.3;
    color: var(--ink-soft);
    font-style: normal;
    margin-bottom: 14px;
  }
  .contact__list { list-style: none; }
  .contact__item {
    display: flex;
    align-items: center;
    gap: 8px;
    font-size: 20px;
    line-height: 1.35;
  }
  .contact__icon {
    width: 16px;
    height: 16px;
    flex: none;
    fill: var(--accent);
  }
</style>
</head>
<body>
<main class="sheet">
  <section class="card card--back" aria-label="Card back">
    <div class="brand brand--embossed">
      <span class="brand__dot"></span>
      <span class="brand__name">Northline<br>Chiropractic</span>
    </div>
  </section>

  <section class="card card--front" aria-label="Card front">
    <div class="brand brand--front">
      <span class="brand__dot"></span>
      <span class="brand__name">Northline<br>Chiropractic</span>
    </div>
    <div class="divider"></div>
    <div class="contact">
      <h1 class="contact__name">Evan Calder</h1>
      <p class="contact__role">President</p>
      <address class="contact__address">1180 Harborview Drive<br>Seacliff CA 90000</address>
      <ul class="contact__list">
        <li class="contact__item">
          <svg class="contact__icon" viewBox="0 0 16 16" aria-hidden="true"><path d="M3.5 1l2.5 3-1.5 1.8c.9 2 2.5 3.6 4.6 4.6L11 8.9l3 2.5-1.3 2.8c-6 .2-11.1-4.9-11-11z"/></svg>
          555-014-2280
        </li>
        <li class="contact__item">
          <svg class="contact__icon" viewBox="0 0 16 16" aria-hidden="true"><path d="M1 3h14v1.2L8 8.6 1 4.2z"/><path d="M1 5.6l7 4.4 7-4.4V13H1z"/></svg>
          evan@northlinechiro.com
        </li>
        <li class="contact__item">
          <svg class="contact__icon" viewBox="0 0 16 16" aria-hidden="true"><circle cx="8" cy="8" r="7"/><path d="M1 8h14M8 1c-3 3.5-3 10.5 0 14M8 1c3 3.5 3 10.5 0 14" stroke="#323234" stroke-width="1" fill="none"/></svg>
          www.northlinechiro.com
        </li>
      </ul>
    </div>
  </section>
</main>
</body>
</html>
```